Corporate Travel Technology Company needs new Business Card design

We need a new business card design to reflect our re-branded company. Our company is called tolvEn (pronounced tolvenn) and we provide Business Intelligence and Smarter Corporate Journeys solutions for the corporate travel industry. Our multinational customers use our solutions to manage large travel budgets and frequent travellers, as well as to save money and reduce risk. We'd like to see designs that use the blue and green palette as well as our corporate logo (attached below). The design should communicate innovation, insight, forward thinking, contemporary, trusted.

Target Market(s)

Large multinational corporates and Travel Agencies.

Industry/Entity Type

Business

Contact Information for Business Card

Rosalind Mercer
Chief Executive
tolvEn
Phone number - +61 (0)2 8134 2907
Email address - rosalind.mercer@tolven-example.com
Mobile number - +61 (0)438 516 702
www.tolven-example.com

Font styles to use
Other font styles liked:
• Please use font as close to corporate logo as possible

Colors
0255a3
0393ce
00a990
33b8a4
33a6d7
3176b5

Requirements
Must have
• Please include the words;
• Smarter Corporate Journeys
• Clear Data Behind Every Business Trip
• Use corporate logo - although icon can be stylised if needed

```html
<!DOCTYPE html>
<html lang="en">
<head>
<meta charset="utf-8">
<title>tolven — Business Card</title>
<link rel="stylesheet" href="https://fonts.googleapis.com/css2?family=Open+Sans:wght@400;600;700&display=swap">
<style>
  :root {
    --backdrop: #eceff2;
    --card-white: #ffffff;
    --brand-blue: #29a9e1;
    --brand-blue-deep: #0aaeee;
    --emboss: #0c9fd8;
    --ink-slate: #3b4d57;
    --ink-dark: #3a474f;
    --white: #ffffff;
  }
  * { margin: 0; padding: 0; box-sizing: border-box; }
  html, body {
    width: 1200px; height: 900px; overflow: hidden;
    background: var(--backdrop);
    font-family: "Open Sans", Arial, sans-serif;
  }
  .canvas { position: relative; width: 1200px; height: 900px; }
  .card {
    position: absolute; overflow: hidden;
    box-shadow: 0 6px 18px rgba(0,0,0,0.18);
  }
  .card-front { left: 237px; top: 62px; width: 556px; height: 342px; background: var(--card-white); }
  .card-back { left: 457px; top: 518px; width: 560px; height: 342px; background: var(--brand-blue-deep); }
  .card svg { position: absolute; left: 0; top: 0; }
  .wordmark {
    position: absolute; left: 0; text-align: center;
    font-weight: 400; letter-spacing: 1px; line-height: 1;
  }
  .card-front .wordmark {
    width: 556px; top: 62px;
    font-size: 70px; color: var(--ink-slate);
  }
  .card-back .wordmark {
    width: 560px; top: 84px;
    font-size: 96px; color: var(--emboss);
  }
  .identity {
    position: absolute; right: 292px; top: 246px; text-align: right; color: var(--white);
  }
  .identity .name { font-size: 17px; font-weight: 700; }
  .identity .role { font-size: 14px; margin-top: 3px; }
  .contacts {
    position: absolute; left: 283px; top: 237px; list-style: none; color: var(--white);
    font-size: 13.5px;
  }
  .contacts li { display: flex; align-items: center; height: 20px; }
  .contacts svg { position: static; width: 11px; height: 11px; margin-right: 9px; flex: none; }
  .tagline {
    position: absolute; left: 0; width: 560px; top: 264px; text-align: center;
    color: var(--ink-dark); font-size: 15.5px; font-weight: 600; line-height: 21px;
  }
</style>
</head>
<body>
<main class="canvas">

  <section class="card card-front" aria-label="Business card front">
    <svg width="556" height="342" viewBox="0 0 556 342" aria-hidden="true">
      <rect x="0" y="190" width="556" height="152" fill="var(--brand-blue)"/>
      <polygon points="0,171 520,171 520,160 556,181 520,205 520,190 0,190"
               fill="var(--brand-blue)" stroke="var(--white)" stroke-width="4" stroke-linejoin="miter"/>
    </svg>
    <div class="wordmark">tolven</div>

    <div class="identity">
      <div class="name">Rosalind Mercer</div>
      <div class="role">Chief Executive</div>
    </div>

    <ul class="contacts">
      <li>
        <svg viewBox="0 0 12 12"><path d="M2.5 1 L4.5 1 L5.2 3.6 L4 4.6 Q5 7 7.4 8 L8.4 6.8 L11 7.5 L11 9.5 Q10.5 11 9 11 Q1 10 1 3 Q1 1.5 2.5 1Z" fill="var(--white)"/></svg>
        +61 (0)2 8134 2907
      </li>
      <li>
        <svg viewBox="0 0 12 12"><rect x="3" y="0.5" width="6" height="11" rx="1" fill="none" stroke="var(--white)" stroke-width="1.3"/><circle cx="6" cy="9.5" r="0.8" fill="var(--white)"/></svg>
        +61 (0)438 516 702
      </li>
      <li>
        <svg viewBox="0 0 12 12"><rect x="1" y="2.5" width="10" height="7" fill="var(--white)"/><path d="M1 2.5 L6 6.5 L11 2.5" fill="none" stroke="var(--brand-blue)" stroke-width="1"/></svg>
        rosalind.mercer@tolven-example.com
      </li>
      <li>
        <svg viewBox="0 0 12 12"><circle cx="6" cy="6" r="5" fill="none" stroke="var(--white)" stroke-width="1.2"/><ellipse cx="6" cy="6" rx="2.2" ry="5" fill="none" stroke="var(--white)" stroke-width="1"/><line x1="1" y1="6" x2="11" y2="6" stroke="var(--white)" stroke-width="1"/></svg>
        www.tolven-example.com
      </li>
    </ul>
  </section>

  <section class="card card-back" aria-label="Business card back">
    <svg width="560" height="342" viewBox="0 0 560 342" aria-hidden="true">
      <polygon points="0,252 473,252 473,234 560,285 473,334 473,318 0,318" fill="var(--white)"/>
    </svg>
    <div class="wordmark">tolven</div>
    <p class="tagline">Smarter Corporate Journeys<br>Clear Data Behind Every Business Trip</p>
  </section>

</main>
</body>
</html>
```